RTavenor Business Cards & Letterhead

I have a logo but need a design for some new business cards. We are a Design-Build Firm that specializes in the design and construction of commercial projects.
the cards need to be professional. no cartoon stuff.
i would like to have the cards in AI format so I can update the card as needed. Logo is provided.
Our Address is: 4187 Marlowe Ct. Fernwick, Vermont 27614

```html
<!DOCTYPE html>
<html lang="en">
<head>
<meta charset="utf-8">
<title>RTavenor Business Card</title>
<link href="https://fonts.googleapis.com/css2?family=Montserrat:wght@400;500;700;800&display=swap" rel="stylesheet">
<style>
  :root {
    --stage: #3b3b3d;
    --card-white: #ffffff;
    --card-dark: #222222;
    --brand-blue: #1474b8;
    --ink: #1e1e1e;
    --ink-soft: #2a2a2a;
  }
  * { margin: 0; padding: 0; box-sizing: border-box; }
  html, body {
    width: 1200px; height: 1059px; overflow: hidden;
    background: var(--stage);
    font-family: "Montserrat", Arial, sans-serif;
  }
  .card {
    position: absolute; left: 256px; width: 688px; height: 391px;
    border-radius: 18px; overflow: hidden;
    box-shadow: 0 10px 22px rgba(0,0,0,.45);
  }
  .card-front { top: 100px; background: var(--card-white); }
  .card-back { top: 537px; background: var(--card-dark); }

  .brand {
    position: absolute; display: flex; align-items: center;
    font-weight: 800; letter-spacing: 0.5px; line-height: 1;
  }
  .brand-square { background: var(--brand-blue); flex: none; }
  .card-front .brand { right: 46px; top: 51px; font-size: 54px; color: var(--ink); gap: 10px; }
  .card-front .brand-square { width: 34px; height: 34px; }
  .card-back .brand { left: 0; right: 0; top: 162px; justify-content: center; font-size: 76px; color: #ffffff; gap: 14px; }
  .card-back .brand-square { width: 50px; height: 50px; }

  .accent-bar { position: absolute; left: 0; top: 153px; width: 15px; height: 39px; background: var(--brand-blue); }
  .person-name {
    position: absolute; left: 29px; top: 148px; line-height: 1;
    font-size: 29px; font-weight: 700; color: var(--brand-blue); letter-spacing: 0.5px;
  }
  .person-title {
    position: absolute; left: 29px; top: 178px; line-height: 1;
    font-size: 18px; font-weight: 400; color: var(--ink-soft); letter-spacing: 0.6px;
  }
  .rule { position: absolute; left: 139px; right: 29px; top: 187px; height: 1.5px; background: var(--brand-blue); }

  .contact-list { position: absolute; left: 28px; top: 216px; list-style: none; }
  .contact-list li {
    display: flex; align-items: center; gap: 8px; height: 26.5px;
    font-size: 16px; color: var(--ink-soft); letter-spacing: 0.4px;
  }
  .contact-list svg { width: 13px; height: 13px; flex: none; }

  .address {
    position: absolute; right: 29px; top: 247px; text-align: right;
    font-size: 16px; line-height: 23px; color: var(--ink-soft); font-style: normal; letter-spacing: 0.4px;
  }
  .wave { position: absolute; left: 0; top: 0; width: 688px; height: 391px; }
</style>
</head>
<body>

<section class="card card-front">
  <div class="brand"><span class="brand-square"></span>RTAVENOR</div>

  <span class="accent-bar"></span>
  <h1 class="person-name">JONAH BREWER</h1>
  <p class="person-title">MANAGER</p>
  <span class="rule"></span>

  <ul class="contact-list">
    <li>
      <svg viewBox="0 0 16 16"><path fill="#1474b8" d="M3.6 1.2l2.2 2.6-1.3 1.6c.8 1.9 2.3 3.4 4.2 4.2l1.6-1.3 2.6 2.2-1.2 2.3C7 12.6 3.4 9 1.2 3.7z"/><path fill="none" stroke="#1474b8" stroke-width="1.3" d="M9.5 4a3 3 0 0 1 2.5 2.5M9.8 1.3a5.7 5.7 0 0 1 4.9 4.9"/></svg>
      555-014-2738
    </li>
    <li>
      <svg viewBox="0 0 16 16"><rect x="1" y="3" width="14" height="10" rx="1" fill="#1474b8"/><path d="M1.5 4l6.5 5 6.5-5" fill="none" stroke="#fff" stroke-width="1.3"/></svg>
      hello@rtavenor.com
    </li>
    <li>
      <svg viewBox="0 0 16 16" fill="none" stroke="#1474b8" stroke-width="1.2"><circle cx="8" cy="8" r="6.5"/><ellipse cx="8" cy="8" rx="3" ry="6.5"/><path d="M1.5 8h13M2.5 4.8h11M2.5 11.2h11"/></svg>
      www.rtavenor.com
    </li>
  </ul>

  <address class="address">4187 Marlowe Ct.<br>Fernwick, Vermont 27614</address>

  <svg class="wave" viewBox="0 0 690 392" preserveAspectRatio="none" aria-hidden="true">
    <path fill="#1474b8" d="M0 314 C60 350 130 368 200 367 C330 365 480 300 592 306 C640 309 672 326 690 338 L690 355 C670 343 640 320 592 321 C480 322 330 371 200 372 C130 373 60 356 0 318 Z"/>
    <path fill="#ffffff" d="M0 318 C60 356 130 373 200 372 C330 371 480 322 592 321 C640 320 670 343 690 355 L690 358 C670 347 640 324 592 325 C480 326 330 374 200 375 C130 376 60 359 0 321 Z"/>
    <path fill="#222222" d="M0 321 C60 359 130 376 200 375 C330 374 480 326 592 325 C640 324 670 347 690 358 L690 392 L0 392 Z"/>
  </svg>
</section>

<section class="card card-back">
  <div class="brand"><span class="brand-square"></span>RTAVENOR</div>
</section>

</body>
</html>
```